Business Card Design For A Renovation Contractor Company

We need a business card for a new company based in Singapore, our company name is "RB Tolvane". We are a renovation contractor that builds designs into reality. We build more of F&B restaurants, retail stores and commercial offices. We work very closely with designers. The final design should communicate to our client that we are a company that you can trust, that will plan and complete your project without giving you a headache. I like my client to remember my company as "RB". The beauty of SIMPLE is important.

Industry/Entity Type

Contractor

Requirements
Nice to have
• Black or Red base

```html
<!DOCTYPE html>
<html lang="en">
<head>
<meta charset="utf-8">
<title>RB Tolvane — Business Card</title>
<link href="https://fonts.googleapis.com/css2?family=Questrial&display=swap" rel="stylesheet">
<style>
  :root {
    --page: #ececea;
    --card: #ffffff;
    --ink: #1f1f21;
    --red: #e3222b;
    --grey: #4b4b4d;
    --white: #ffffff;
    --rule: #8a8a8c;
  }
  * { box-sizing: border-box; margin: 0; padding: 0; }
  html, body { width: 1200px; height: 720px; overflow: hidden; }
  body {
    background: var(--page);
    font-family: "Questrial", "Century Gothic", sans-serif;
    color: var(--ink);
    position: relative;
  }
  .card {
    position: absolute;
    top: 205px;
    width: 540px;
    height: 309px;
    background: var(--card);
    box-shadow: 0 2px 8px rgba(0,0,0,0.12);
    overflow: hidden;
  }
  .card--contact { left: 40px; }
  .card--brand { left: 620px; }

  /* contact side */
  .contact-mark {
    position: absolute;
    left: 50%; top: 18px;
    width: 52px; height: 52px;
    margin-left: -26px;
    border: 4px solid var(--ink);
    border-radius: 50%;
  }
  .wordmark {
    position: absolute;
    left: 0; right: 0;
    text-align: center;
    color: var(--ink);
    letter-spacing: 0.5px;
    white-space: nowrap;
  }
  .card--contact .wordmark { top: 80px; font-size: 38px; line-height: 1; }
  .tagline {
    position: absolute;
    left: 0; right: 0;
    text-align: center;
    white-space: nowrap;
  }
  .tagline span {
    display: inline-block;
    border-top: 1.5px solid var(--rule);
    color: var(--ink);
  }
  .card--contact .tagline { top: 124px; }
  .card--contact .tagline span { font-size: 15px; padding: 1px 8px 0; letter-spacing: 0.6px; }

  .band-name {
    position: absolute;
    left: 0; right: 0; top: 160px; height: 34px;
    background: var(--grey);
    color: var(--white);
    display: flex; align-items: center; justify-content: center;
    gap: 6px;
  }
  .band-name .person { font-size: 18px; font-weight: 700; letter-spacing: 0.3px; }
  .band-name .role { font-size: 13px; }

  .band-info {
    position: absolute;
    left: 0; right: 0; top: 194px; bottom: 0;
    background: var(--red);
    color: var(--white);
    text-align: center;
    font-size: 14px;
    letter-spacing: 0.6px;
    padding-top: 16px;
  }
  .band-info p { margin-bottom: 10px; display: flex; justify-content: center; align-items: center; gap: 14px; }
  .band-info .item { display: inline-flex; align-items: center; gap: 5px; }
  .band-info svg { width: 12px; height: 12px; fill: var(--white); }
  .band-info .web { letter-spacing: 3px; }

  /* brand side */
  .card--brand .wordmark { top: 100px; font-size: 56px; line-height: 1; }
  .card--brand .tagline { top: 164px; }
  .card--brand .tagline span { font-size: 22px; padding: 1px 10px 0; letter-spacing: 0.8px; }
  .site {
    position: absolute;
    right: 44px; bottom: 36px;
    font-size: 17px;
    letter-spacing: 4px;
    color: var(--ink);
  }
</style>
</head>
<body>

<section class="card card--contact">
  <div class="contact-mark"></div>
  <div class="wordmark">RB Tolvane</div>
  <div class="tagline"><span>solid work from a clear plan</span></div>

  <div class="band-name">
    <span class="person">Your Name,</span><span class="role">Title</span>
  </div>

  <div class="band-info">
    <p>
      <span class="item">
        <svg viewBox="0 0 24 24" aria-hidden="true"><path d="M6.6 10.8a15 15 0 0 0 6.6 6.6l2.2-2.2c.3-.3.7-.4 1-.2 1.1.4 2.3.6 3.6.6.6 0 1 .4 1 1V20c0 .6-.4 1-1 1C10.6 21 3 13.4 3 4c0-.6.4-1 1-1h3.5c.6 0 1 .4 1 1 0 1.3.2 2.5.6 3.6.1.3 0 .7-.2 1z"/></svg>
        555-201-7843
      </span>
      <span class="item">
        <svg viewBox="0 0 24 24" aria-hidden="true"><path d="M7 1h10a2 2 0 0 1 2 2v18a2 2 0 0 1-2 2H7a2 2 0 0 1-2-2V3a2 2 0 0 1 2-2zm0 4v13h10V5zm5 14.5a1.2 1.2 0 1 0 0 2.4 1.2 1.2 0 0 0 0-2.4z"/></svg>
        555-309-6612
      </span>
      <span class="item">
        <svg viewBox="0 0 24 24" aria-hidden="true"><path d="M3 5h18a1 1 0 0 1 1 1v12a1 1 0 0 1-1 1H3a1 1 0 0 1-1-1V6a1 1 0 0 1 1-1zm1 2.2V17h16V7.2l-8 5.3z"/></svg>
        info@rbtolvane.com
      </span>
    </p>
    <p class="web">www.rbtolvane.com</p>
    <p>Door No. Street Name City Name, State, Zip Code.</p>
  </div>
</section>

<section class="card card--brand">
  <div class="wordmark">RB Tolvane</div>
  <div class="tagline"><span>solid work from a clear plan</span></div>
  <div class="site">www.rbtolvane.com</div>
</section>

</body>
</html>
```